New Business Card for Software Company

We are looking at rebranding a 10 year old company that specializes in PDF and DWF solutions for Architects and Engineers. We will attach the new company logo that we are going with so you can work with that and complimentary colors.
The sample information we would like on the business card is:
Gerald Pinfold
Vice President
4738 W. Harrowgate Lane. STE 305
PMB#417
Mesa, AZ 85374
866-392-5074 US Toll Free
123-456-3190 Cell
gpinfold@plavorix.com
The old tag line that we had on the business cars was.
Providing Industrial Strength PDF and DWF Solutions to the Global CAD Marketplace.
If you have an idea for a better tag line we are open to that also.
Updates
We would like to thank all of the Designers for their wonderful work. We apologize that we will not have the time to provide feedback to everyone. There is just so many innovative and professional designs that you have all created making our decision even harder.
Target Market(s)
Architects and Engineers
Industry/Entity Type
Business
Look and feel

```html
<!DOCTYPE html>
<html lang="en">
<head>
<meta charset="utf-8">
<title>Plavorix Business Card</title>
<link rel="stylesheet" href="https://fonts.googleapis.com/css2?family=Source+Sans+3:ital,wght@0,700;1,700&display=swap">
<style>
  :root {
    --bg-edge: #d5e8b8;
    --bg-mid: #8cc63f;
    --card-white: #ffffff;
    --orange-deep: #f05a28;
    --orange-mid: #f7941d;
    --orange-pale: #fde2c8;
    --ink: #1a1a1a;
    --brand-grey: #5f6062;
    --brand-orange: #f26a2e;
  }
  * { margin: 0; padding: 0; box-sizing: border-box; }
  html, body { width: 1200px; height: 914px; overflow: hidden; }
  body {
    position: relative;
    font-family: "Source Sans 3", "Myriad Pro", sans-serif;
    background: linear-gradient(90deg, var(--bg-edge) 0%, var(--bg-mid) 50%, var(--bg-edge) 100%);
  }
  .card {
    position: absolute;
    background: var(--card-white);
    overflow: hidden;
  }
  .card-front { left: 102px; top: 41px; width: 662px; height: 377px; }
  .card-back { left: 443px; top: 468px; width: 660px; height: 377px; }
  .card-swoosh { position: absolute; inset: 0; width: 100%; height: 100%; }

  .brand {
    position: absolute;
    display: flex;
    align-items: center;
    font-weight: 700;
    color: var(--brand-grey);
    letter-spacing: -0.02em;
  }
  .brand-dot { border-radius: 50%; background: var(--brand-orange); flex: none; }
  .card-front .brand { left: 100px; top: 40px; font-size: 76px; gap: 22px; }
  .card-front .brand-dot { width: 78px; height: 78px; }
  .card-back .brand { left: 190px; top: 60px; font-size: 44px; gap: 12px; }
  .card-back .brand-dot { width: 48px; height: 48px; }

  .tagline {
    position: absolute;
    font-weight: 700;
    font-style: italic;
    font-size: 15px;
    color: var(--ink);
    white-space: nowrap;
  }
  .tagline-one { left: 102px; top: 136px; }
  .tagline-two { left: 213px; top: 163px; }

  .person {
    position: absolute;
    left: 91px; top: 237px;
    font-weight: 700;
    font-style: italic;
    font-size: 19px;
    line-height: 24px;
    color: var(--ink);
  }
  .contact {
    position: absolute;
    left: 329px; top: 199px;
    font-weight: 700;
    font-size: 16px;
    line-height: 21px;
    color: var(--ink);
    font-style: normal;
  }
</style>
</head>
<body>
  <section class="card card-front">
    <svg class="card-swoosh" viewBox="0 0 662 377" aria-hidden="true">
      <defs>
        <linearGradient id="frontFade" x1="0" y1="0" x2="1" y2="0">
          <stop offset="0" stop-color="#f05a28"/>
          <stop offset="0.1" stop-color="#f7941d"/>
          <stop offset="0.36" stop-color="#fde2c8"/>
          <stop offset="0.5" stop-color="#ffffff"/>
          <stop offset="0.64" stop-color="#fde2c8"/>
          <stop offset="0.9" stop-color="#f7941d"/>
          <stop offset="1" stop-color="#f05a28"/>
        </linearGradient>
      </defs>
      <rect width="662" height="377" fill="url(#frontFade)"/>
      <path d="M0,0 C20,250 200,377 331,377 C462,377 642,250 662,0 Z" fill="#ffffff"/>
    </svg>
    <div class="brand"><span class="brand-dot"></span>Plavorix</div>
    <p class="tagline tagline-one">Providing Industrial Strength PDF and DWF</p>
    <p class="tagline tagline-two">Solutions to the Global CAD Marketplace ..........</p>
  </section>

  <section class="card card-back">
    <svg class="card-swoosh" viewBox="0 0 660 377" aria-hidden="true">
      <defs>
        <linearGradient id="backFade" x1="0" y1="0" x2="1" y2="0">
          <stop offset="0" stop-color="#f05a28"/>
          <stop offset="0.1" stop-color="#f7941d"/>
          <stop offset="0.36" stop-color="#fde2c8"/>
          <stop offset="0.5" stop-color="#ffffff"/>
          <stop offset="0.64" stop-color="#fde2c8"/>
          <stop offset="0.9" stop-color="#f7941d"/>
          <stop offset="1" stop-color="#f05a28"/>
        </linearGradient>
      </defs>
      <rect width="660" height="377" fill="url(#backFade)"/>
      <path d="M0,377 C20,127 200,0 330,0 C460,0 640,127 660,377 Z" fill="#ffffff"/>
    </svg>
    <div class="brand"><span class="brand-dot"></span>Plavorix</div>
    <p class="person">Gerald Pinfold<br>Vice President</p>
    <address class="contact">
      4738 W. Harrowgate Lane. STE 305<br>
      PMB#417<br>
      Mesa, AZ 85374<br>
      866-392-5074 US Toll Free<br>
      123-456-3190 Cell<br>
      gpinfold@plavorix.com
    </address>
  </section>
</body>
</html>
```